Small butcher shop from Austria needs great powerpoint presentation

We are looking for a powerpoint template for our new CI - it should be modern and clear.

Logo (2 Versions), Slogan, Business Card and Car-Wrap-Design already exist. (See documents below.)

We won't use much text. About 50% of the presentation should be pictures, included in different ways.

We are a family business in Upper Austria, only process animals from farms in the immediate vicinity, produce the products by hand, value animal welfare and short transport routes and avoid packaging as much as possible.

The design should be modern and clear.

Sans Serif

• Use the red color sparingly. Only use sans serif fonts (Myriad Pro - if possible). The logo needs to be on first and last page only.

```html
<!DOCTYPE html>
<html lang="de">
<head>
<meta charset="utf-8">
<title>Holzer Fleischhauerei – Präsentation</title>
<link rel="stylesheet" href="https://fonts.googleapis.com/css2?family=Source+Sans+3:wght@400;600;700;900&family=Arimo:wght@400&display=swap">
<style>
:root{
  --page:#dcdde0;
  --paper:#ffffff;
  --maroon:#6e0b1e;
  --ink:#1d1d1d;
  --body:#4a4a4a;
  --night:#1f2326;
}
*{box-sizing:border-box;margin:0;padding:0}
html,body{width:1200px;height:4231px;overflow:hidden;background:var(--page)}
body{position:relative;font-family:"Source Sans 3",sans-serif;color:var(--ink)}
.slide{position:absolute;left:36px;width:1129px;height:636px;background:var(--paper);overflow:hidden;box-shadow:0 1px 4px rgba(0,0,0,.25)}
.slide-num{position:absolute;left:14px;bottom:12px;font-weight:700;font-size:18px}
.slide-num.right{left:auto;right:14px}
.on-dark .slide-num{color:#fff}
.abs{position:absolute}
.photo{position:absolute}
.kicker{font-size:30px;color:var(--maroon);font-weight:400}
.headline{font-weight:900;line-height:1.1;text-transform:uppercase;color:var(--ink)}
.lorem{font-family:"Arimo",sans-serif;color:var(--body);font-size:12.5px;line-height:2}
.caption{position:absolute;left:0;right:0;bottom:14px;text-align:center;color:#fff;font-weight:700;font-size:15px}

/* slide 1 & 6 */
.hero-bg{position:absolute;inset:0;background:linear-gradient(160deg,#3a3d3a 0%,#262a2b 45%,#1a1d1e 100%)}
.hero-title{position:absolute;left:0;right:0;text-align:center;color:#fff;font-weight:900;text-transform:uppercase;line-height:1.3}
.brand-box{position:absolute;left:30px;top:2px;width:121px;height:121px;background:var(--maroon);display:flex;align-items:center;justify-content:center;color:#fff;font-weight:700;font-size:26px;letter-spacing:1px}
.brand-line{position:absolute;left:0;right:0;text-align:center;color:#fff;font-weight:700;font-size:52px;letter-spacing:2px}

/* slide 2 */
.ticks{list-style:none;position:absolute;left:30px;top:485px;font-size:16px;color:#333}
.ticks li{display:flex;align-items:center;gap:10px;height:31px}

/* slide 3 */
.service{position:absolute;top:163px;width:323px}
.service .photo{position:relative;height:291px;box-shadow:0 2px 5px rgba(0,0,0,.3)}
.service h3{margin-top:12px;text-align:center;color:var(--maroon);font-weight:900;font-size:22px;text-transform:uppercase}
.service p{margin-top:4px;text-align:center;font-family:"Arimo",sans-serif;font-size:10.5px;line-height:2.05;color:var(--body)}

/* slide 4 */
.phone-box{position:absolute;left:417px;top:499px;width:294px;height:52px;border:1.5px solid #b9a3a8;display:flex;align-items:center}
.phone-box .icon{width:62px;height:100%;background:var(--maroon);display:flex;align-items:center;justify-content:center}
.phone-box span{padding-left:18px;font-size:22px;font-weight:400;color:#222}
</style>
</head>
<body>

<!-- 1 -->
<section class="slide on-dark" style="top:64px">
  <div class="hero-bg" role="img" aria-label="Lieferwagen mit Folierung vor einem alten Bauernhof, abgedunkelt"></div>
  <div class="brand-box">HOLZER</div>
  <h1 class="hero-title" style="top:222px;font-size:72px">Fresh, Safe<br>Quality Meats</h1>
  <span class="slide-num">1</span>
</section>

<!-- 2 -->
<section class="slide" style="top:758px">
  <p class="kicker abs" style="left:30px;top:102px">About Us</p>
  <h2 class="headline abs" style="left:30px;top:140px;font-size:62px">We Provide<br>Best Meat</h2>
  <div class="lorem abs" style="left:30px;top:300px;width:430px">
    <p>Lorem ipsum dolor sit amet, consectetur adipiscing elit, sed do eiusmod tempor incididunt ut labore et dolore magna aliqua. Ut enim ad minim veniam, quis nostrud exercitation</p>
    <p style="margin-top:8px">Lorem ipsum dolor sit amet, consectetur adipiscing elit, sed do eiusmod tempor incididunt ut labore et dolore magna aliqua. Ut enim ad minim veniam, quis nostrud exercitation</p>
  </div>
  <ul class="ticks">
    <li><svg width="13" height="13" viewBox="0 0 14 14"><circle cx="7" cy="7" r="7" fill="var(--maroon)"/><path d="M5.5 4l3 3-3 3" stroke="#fff" stroke-width="2" fill="none"/></svg>100% Organic Meat</li>
    <li><svg width="13" height="13" viewBox="0 0 14 14"><circle cx="7" cy="7" r="7" fill="var(--maroon)"/><path d="M5.5 4l3 3-3 3" stroke="#fff" stroke-width="2" fill="none"/></svg>Payment Securation</li>
  </ul>
  <div class="photo" style="left:488px;top:39px;width:292px;height:558px;background:linear-gradient(180deg,#e9a45a 0%,#a8582d 50%,#5a3420 100%)" role="img" aria-label="Rind auf einer Weide im Abendlicht"></div>
  <div class="photo" style="left:793px;top:39px;width:292px;height:558px;background:linear-gradient(180deg,#6c8fb3 0%,#6b5548 35%,#4a4c4f 65%,#4f7d3c 100%)" role="img" aria-label="Folierter Lieferwagen vor einer Backsteinscheune"></div>
  <span class="slide-num">2</span>
</section>

<!-- 3 -->
<section class="slide" style="top:1453px">
  <p class="kicker abs" style="left:0;right:0;top:34px;text-align:center">What we do</p>
  <h2 class="headline abs" style="left:0;right:0;top:80px;text-align:center;font-size:54px">Services for you</h2>
  <div class="service" style="left:59px">
    <div class="photo" style="background:linear-gradient(180deg,#5a8fd6 0%,#b98a5c 55%,#5f9a3a 100%)" role="img" aria-label="Braun-weißes Rind vor blauem Himmel"></div>
    <h3>Veal Entrecote</h3>
    <p>Lorem ipsum dolor sit amet, consectetur adipiscing elit, sed do eiusmod tempor incididunt ut labore et dolore magna aliqua. Ut enim ad minim veniam, quis nostrud exercitation ullamco laboris nisi ut aliquip ex ea commodo consequat.</p>
  </div>
  <div class="service" style="left:402px">
    <div class="photo" style="background:linear-gradient(180deg,#3d3a36 0%,#8b8680 50%,#a68c6a 100%)" role="img" aria-label="Schwarz-weiße Kühe im Stall beim Fressen"></div>
    <h3>Beef Tenderloin</h3>
    <p>Lorem ipsum dolor sit amet, consectetur adipiscing elit, sed do eiusmod tempor incididunt ut labore et dolore magna aliqua. Ut enim ad minim veniam, quis nostrud exercitation ullamco laboris nisi ut aliquip ex ea commodo consequat.</p>
  </div>
  <div class="service" style="left:745px">
    <div class="photo" style="background:linear-gradient(180deg,#4e5866 0%,#4a5a48 45%,#3f7a2f 100%)" role="img" aria-label="Schwarz-weiße Kuh auf grüner Wiese"></div>
    <h3>Beaf Ribs</h3>
    <p>Lorem ipsum dolor sit amet, consectetur adipiscing elit, sed do eiusmod tempor incididunt ut labore et dolore magna aliqua. Ut enim ad minim veniam, quis nostrud exercitation ullamco laboris nisi ut aliquip ex ea commodo consequat.</p>
  </div>
  <span class="slide-num right">3</span>
</section>

<!-- 4 -->
<section class="slide" style="top:2149px">
  <div class="abs" style="left:0;top:0;width:251px;height:158px;background:radial-gradient(ellipse at 40% 50%,#eeeef0 0%,rgba(255,255,255,0) 70%)" role="img" aria-label="Zarte Strichzeichnung eines Fleischstücks mit Kräutern"></div>
  <div class="abs" style="left:778px;top:462px;width:351px;height:174px;background:radial-gradient(ellipse at 55% 55%,#ececee 0%,rgba(255,255,255,0) 70%)" role="img" aria-label="Zarte Strichzeichnung eines Steaks mit Tomate und Gewürzen"></div>
  <h2 class="headline abs" style="left:0;right:0;top:76px;text-align:center;font-size:44px;color:var(--maroon);line-height:1.25">You can call anytime<br>toget our product</h2>
  <div class="lorem abs" style="left:125px;width:880px;top:200px;text-align:center;font-size:12px;line-height:2.35">
    <p>Sed ut perspiciatis unde omnis iste natus error sit voluptatem accusantium doloremque laudantium, totam rem aperiam, eaque ipsa quae ab illo inventore veritatis et quasi architecto beatae vitae dicta sunt explicabo. Nemo enim ipsam voluptatem quia voluptas sit aspernatur aut odit aut fugit, sed quia consequuntur magni dolores eos qui ratione voluptatem sequi nesciunt. Neque porro quisquam est, qui dolorem ipsum quia dolor sit amet, consectetur, adipisci velit, sed quia non numquam eius modi tempora incidunt ut labore et dolore magnam aliquam quaerat voluptatem. Ut enim ad minima veniam, quis nostrum exercitationem ullam corporis suscipit laboriosam, nisi ut aliquid ex ea commodi consequatur? Quis autem vel eum iure reprehenderit qui in ea voluptate velit esse quam nihil molestiae consequatur, vel illum qui dolorem eum fugiat quo voluptas nulla pariatur</p>
    <p style="margin-top:10px">Sed ut perspiciatis unde omnis iste natus error sit voluptatem accusantium doloremque laudantium, totam rem aperiam, eaque ipsa quae ab illo inventore veritatis et quasi architecto beatae vitae dicta sunt explicabo. Nemo enim ipsam voluptatem quia voluptas sit aspernatur aut odit aut fugit, sed quia consequuntur magni dolores eos qui ratione voluptatem sequi nesciunt. Neque porro quisquam est,</p>
  </div>
  <div class="phone-box">
    <div class="icon"><svg width="18" height="18" viewBox="0 0 24 24"><path fill="#fff" d="M6.6 10.8a15.1 15.1 0 0 0 6.6 6.6l2.2-2.2c.3-.3.7-.4 1-.2 1.1.4 2.3.6 3.6.6.6 0 1 .4 1 1V20c0 .6-.4 1-1 1A17 17 0 0 1 3 4c0-.6.4-1 1-1h3.5c.6 0 1 .4 1 1 0 1.3.2 2.5.6 3.6.1.3 0 .7-.2 1z"/></svg></div>
    <span>+43 660 123 4567</span>
  </div>
  <span class="slide-num">4</span>
</section>

<!-- 5 -->
<section class="slide" style="top:2843px">
  <h2 class="headline abs" style="left:30px;top:28px;font-size:54px">Our Gallery</h2>
  <div class="lorem abs" style="left:30px;top:104px;width:505px;font-size:12px;line-height:2.3">
    <p>Sed ut perspiciatis unde omnis iste natus error sit voluptatem accusantium doloremque laudantium, totam rem aperiam, eaque ipsa quae ab illo inventore veritatis et quasi architecto beatae vitae dicta sunt explicabo. Nemo enim ipsam voluptatem quia voluptas sit aspernatur aut odit aut fugit, sed quia consequuntur magni dolores eos qui ratione voluptatem sequi nesciunt. Neque porro quisquam est,</p>
    <p style="margin-top:6px">Sed ut perspiciatis unde omnis iste natus error sit voluptatem accusantium doloremque laudantium, totam rem aperiam, eaque ipsa quae ab illo inventore veritatis et quasi architecto beatae vitae dicta sunt explicabo</p>
  </div>
  <div class="photo" style="left:565px;top:33px;width:218px;height:299px;background:linear-gradient(180deg,#4b4642 0%,#6a4a36 50%,#9c8a62 100%)" role="img" aria-label="Kühe im Stall beim Fressen"><p class="caption">Lorem ipsum dolor sit amet</p></div>
  <div class="photo" style="left:795px;top:33px;width:295px;height:299px;background:linear-gradient(180deg,#8c949e 0%,#b9b2ab 50%,#74734f 100%)" role="img" aria-label="Junges Rind auf einer Weide"><p class="caption">Lorem ipsum dolor sit amet</p></div>
  <div class="photo" style="left:31px;top:361px;width:515px;height:253px;background:linear-gradient(180deg,#4c7a3a 0%,#3f6d2c 40%,#6b9a3c 100%)" role="img" aria-label="Herde grasender Kühe vor Bäumen"><p class="caption">Lorem ipsum dolor sit amet</p></div>
  <div class="photo" style="left:565px;top:348px;width:295px;height:266px;background:linear-gradient(180deg,#3e3a1e 0%,#c69a3a 45%,#8a6a28 100%)" role="img" aria-label="Kühe auf einer Weide im Gegenlicht"><p class="caption" style="font-size:13px">Lorem ipsum dolor sit amet</p></div>
  <div class="photo" style="left:869px;top:348px;width:218px;height:266px;background:linear-gradient(180deg,#58703e 0%,#4a5e32 50%,#6f7a4e 100%)" role="img" aria-label="Rinder auf einem Almweg"><p class="caption" style="font-size:13px">Lorem ipsum dolor sit amet</p></div>
  <span class="slide-num">5</span>
</section>

<!-- 6 -->
<section class="slide on-dark" style="top:3539px">
  <div class="hero-bg" style="background:linear-gradient(160deg,#2b2e2d 0%,#1e2122 50%,#151718 100%)" role="img" aria-label="Folierter Lieferwagen vor einem Bauernhof, stark abgedunkelt"></div>
  <p class="brand-line" style="top:218px">HOLZER</p>
  <h1 class="hero-title" style="top:310px;font-size:54px;line-height:1.22">Weil Regionales besser<br>schmeckt</h1>
  <span class="slide-num">6</span>
</section>

</body>
</html>
```